New Website for World Wide Charity (KOLVAN)

We need a dynamic web design for our brand new charity organisation that will be working worldwide. We will be funded by donations so need to attract people to donate.

What We Do
We work to optimise the wellbeing of the planet, the animals and all that live within. Our slogan is Achieving Vibrational Equilibrium.

We have included a Powerpoint document which may help you understand what we need, it is just an idea for structure and style, it is not set in stone so feel free to be as creative as you like!
Updates

Designs look the same

Target Market(s)

Adults 18+ with an interest in animal, environmental. Businesses that may like to support our natural world or already support our natural world.

Number of Pages Required

3 page

Colors

Designer to choose colors to be used in the design.

Requirements
Must have
• We need the website to be easy to use and understand.

Web pages will be Home, What We Do, Who We Are, Success Stories, What You Can Do (Blog section), Seek Help, Donate, Join.
Nice to have
• Natural feel, easy to navigate, Ideally the website will look natural and organic.

Natural colours, blues, greens, sand, gold, brown, grey, silver, Orange and yellow for impact.
Should not have
• Should not have a dark coloured theme.

```html
<!DOCTYPE html>
<html lang="en">
<head>
<meta charset="utf-8">
<title>Kolvan — Help Raise World Vibration</title>
<link rel="stylesheet" href="https://fonts.googleapis.com/css2?family=Raleway:wght@300;500;600&family=Roboto:wght@400;500&display=swap">
<style>
  :root {
    --ink: #111111;
    --body-text: #6b6b6b;
    --white: #ffffff;
    --lavender: #ddd0e2;
    --lavender-soft: #d9c6de;
    --footer-bg: #3a3a3b;
    --footer-line: #555556;
    --footer-text: #f2f2f2;
    --brand-blue: #3d5d9a;
  }
  * { box-sizing: border-box; margin: 0; padding: 0; }
  html, body { width: 1200px; height: 2826px; overflow: hidden; background: var(--white); }
  body { position: relative; font-family: "Roboto", Arial, sans-serif; color: var(--ink); }
  .abs { position: absolute; }

  /* header */
  .site-header { left: 0; top: 0; width: 1200px; height: 70px; background: var(--white); z-index: 3; }
  .brand-badge { left: 108px; top: 6px; width: 122px; height: 122px; border-radius: 50%; background: var(--white);
    border: 5px solid #eeebf1; box-shadow: 0 2px 6px rgba(0,0,0,.18); display: flex; align-items: center; justify-content: center;
    font-weight: 500; font-size: 17px; letter-spacing: 1px; color: var(--brand-blue); z-index: 4; }
  .main-nav { right: 116px; top: 29px; display: flex; gap: 23px; font-size: 14.5px; font-weight: 500; letter-spacing: .4px; }
  .main-nav a { color: var(--ink); text-decoration: none; }
  .main-nav a.is-current { color: var(--lavender-soft); font-weight: 400; }

  /* hero */
  .hero { left: 0; top: 70px; width: 1200px; height: 557px;
    background:
      radial-gradient(ellipse 320px 110px at 760px 60px, rgba(246,214,160,.85), rgba(246,214,160,0) 100%),
      radial-gradient(ellipse 260px 90px at 250px 40px, rgba(240,200,170,.7), rgba(240,200,170,0) 100%),
      radial-gradient(ellipse 520px 150px at 300px 290px, rgba(103,140,170,.75), rgba(103,140,170,0) 100%),
      radial-gradient(ellipse 560px 170px at 880px 270px, rgba(96,128,168,.75), rgba(96,128,168,0) 100%),
      radial-gradient(ellipse 260px 240px at 600px 470px, rgba(200,225,200,.55), rgba(200,225,200,0) 100%),
      radial-gradient(ellipse 200px 150px at 1010px 470px, rgba(205,230,200,.55), rgba(205,230,200,0) 100%),
      radial-gradient(ellipse 160px 170px at 250px 450px, rgba(205,230,205,.5), rgba(205,230,205,0) 100%),
      radial-gradient(ellipse 400px 200px at 100px 480px, rgba(62,120,70,.6), rgba(62,120,70,0) 100%),
      radial-gradient(ellipse 360px 200px at 1150px 430px, rgba(120,175,70,.7), rgba(120,175,70,0) 100%),
      linear-gradient(180deg, #bba9cc 0%, #d7b6bf 12%, #e3c3b0 20%, #aab0cf 32%, #8ca6c0 42%, #739c9a 52%, #6d9f7c 64%, #6fa464 78%, #7fb35d 90%, #8cbf66 100%); }
  .hero-title { left: 0; top: 163px; width: 1200px; text-align: center; font-family: "Raleway", sans-serif; font-weight: 300;
    font-size: 45px; color: var(--white); letter-spacing: .5px; }
  .hero-sub { left: 0; top: 237px; width: 1200px; text-align: center; font-size: 15.5px; color: var(--white); }
  .btn { display: flex; align-items: center; justify-content: center; gap: 10px; background: var(--lavender);
    color: var(--ink); font-weight: 500; font-size: 15px; letter-spacing: .3px; border-radius: 3px; text-decoration: none; }
  .btn svg { width: 13px; height: 13px; }
  .hero-btn { left: 494px; top: 287px; width: 212px; height: 50px; }

  /* category cards */
  .cat-card { top: 732px; width: 316px; height: 229px; overflow: hidden; }
  .cat-card.environment { left: 112px; background:
      radial-gradient(ellipse 80px 70px at 150px 60px, rgba(150,200,70,.9), rgba(150,200,70,0) 100%),
      radial-gradient(ellipse 150px 45px at 120px 120px, rgba(70,110,30,.9), rgba(70,110,30,0) 100%),
      radial-gradient(ellipse 140px 80px at 260px 200px, rgba(214,160,120,.75), rgba(214,160,120,0) 100%),
      radial-gradient(ellipse 180px 110px at 280px 30px, rgba(225,210,110,.8), rgba(225,210,110,0) 100%),
      linear-gradient(160deg, #a8b84a 0%, #6d9d39 40%, #3f7a27 75%, #2b5a1f 100%); }
  .cat-card.animal { left: 442px; background:
      radial-gradient(ellipse 110px 90px at 165px 100px, #555 0%, #7d7d7d 45%, rgba(170,170,170,0) 100%),
      linear-gradient(90deg, #d4d4d4 0%, #f0f0f0 35%, #e6e6e6 70%, #f4f4f4 100%); }
  .cat-card.human { left: 772px; background:
      radial-gradient(ellipse 60px 50px at 175px 45px, rgba(110,70,50,.9), rgba(110,70,50,0) 100%),
      radial-gradient(ellipse 85px 90px at 175px 170px, rgba(215,225,225,.95), rgba(215,225,225,0) 100%),
      linear-gradient(90deg, #2f3840 0%, #6f7b84 30%, #a6b1b7 50%, #55616a 75%, #1f262c 100%); }
  .cat-card::after { content: ""; position: absolute; inset: 0; background: linear-gradient(180deg, rgba(0,0,0,0) 50%, rgba(0,0,0,.25) 100%); }
  .cat-label { left: 0; width: 100%; text-align: center; color: var(--white); z-index: 1; }
  .cat-label .name { display: block; margin-top: 147px; font-size: 19px; font-weight: 500; letter-spacing: 1px; text-shadow: 0 1px 3px rgba(0,0,0,.35); }
  .cat-label .more { display: inline-flex; align-items: center; gap: 8px; margin-top: 7px; font-size: 12px; font-weight: 500;
    letter-spacing: .4px; text-decoration: underline; color: var(--white); }
  .cat-label .more svg { width: 11px; height: 11px; }

  /* feature rows */
  .feature-img { width: 448px; height: 342px; }
  .feature-img.environment { left: 111px; top: 1090px; background:
      radial-gradient(ellipse 70px 70px at 228px 180px, #f3f5c0 0%, #a6d35a 45%, rgba(100,160,50,0) 100%),
      radial-gradient(ellipse 125px 125px at 228px 175px, rgba(230,240,200,.35), rgba(230,240,200,0) 100%),
      radial-gradient(ellipse 110px 45px at 270px 270px, rgba(225,180,150,.9), rgba(225,180,150,0) 100%),
      radial-gradient(ellipse 220px 120px at 80px 60px, rgba(45,80,30,.8), rgba(45,80,30,0) 100%),
      linear-gradient(180deg, #6d9a3f 0%, #86b450 45%, #7fb24a 70%, #5f9637 100%); }
  .feature-img.animal { left: 641px; top: 1527px; background:
      radial-gradient(ellipse 150px 55px at 200px 135px, rgba(235,235,225,.95), rgba(235,235,225,0) 100%),
      radial-gradient(ellipse 100px 65px at 260px 175px, rgba(25,25,20,.85), rgba(25,25,20,0) 100%),
      linear-gradient(170deg, rgba(0,0,0,0) 52%, rgba(75,55,40,.85) 55%, rgba(75,55,40,.85) 62%, rgba(0,0,0,0) 65%),
      radial-gradient(ellipse 200px 150px at 60px 60px, rgba(140,165,110,.8), rgba(140,165,110,0) 100%),
      linear-gradient(160deg, #6a8453 0%, #4f6b3a 40%, #3d5530 75%, #566e3c 100%); }
  .feature-img.human { left: 111px; top: 1964px; background:
      radial-gradient(ellipse 70px 85px at 245px 145px, rgba(130,80,50,.95), rgba(130,80,50,0) 100%),
      radial-gradient(ellipse 110px 90px at 245px 300px, rgba(240,235,225,.95), rgba(240,235,225,0) 100%),
      radial-gradient(ellipse 130px 200px at 380px 160px, rgba(185,170,100,.85), rgba(185,170,100,0) 100%),
      radial-gradient(ellipse 170px 150px at 70px 250px, rgba(200,150,100,.85), rgba(200,150,100,0) 100%),
      linear-gradient(180deg, #e6e2da 0%, #dcd1c0 40%, #c9a37a 75%, #a67f55 100%); }
  .feature-title { font-family: "Raleway", sans-serif; font-weight: 600; font-size: 31px; letter-spacing: .5px; color: var(--ink); }
  .feature-text { width: 430px; font-size: 14.6px; line-height: 28.3px; color: var(--body-text); }
  .feature-btn { width: 161px; height: 50px; }

  /* footer */
  .site-footer { left: 0; top: 2425px; width: 1200px; height: 401px; background:
      radial-gradient(ellipse 300px 120px at 560px 40px, rgba(80,80,82,.6), rgba(80,80,82,0) 100%),
      linear-gradient(180deg, var(--footer-bg) 0%, var(--footer-bg) 60%, #2e2e2f 100%); color: var(--footer-text); }
  .footer-col { top: 76px; }
  .footer-col h3 { font-size: 14.5px; font-weight: 500; letter-spacing: .4px; }
  .footer-col .rule { width: 28px; height: 2px; background: var(--footer-text); margin-top: 11px; }
  .footer-col ul { list-style: none; margin-top: 17px; }
  .footer-col li { height: 38.5px; font-size: 14.5px; display: flex; align-items: flex-start; gap: 12px; }
  .footer-col li svg { width: 10px; height: 10px; margin-top: 5px; }
  .footer-badge { left: 884px; top: 59px; width: 186px; height: 186px; border-radius: 50%; background: var(--white);
    display: flex; align-items: center; justify-content: center; font-size: 26px; font-weight: 500; letter-spacing: 2px; color: var(--brand-blue); }
  .footer-divider { left: 120px; top: 307px; width: 960px; height: 1px; background: var(--footer-line); }
  .copyright { left: 0; top: 347px; width: 1200px; text-align: center; font-size: 14.5px; }
</style>
</head>
<body>
<svg width="0" height="0" style="position:absolute">
  <symbol id="arrow-circle" viewBox="0 0 16 16"><circle cx="8" cy="8" r="8" fill="currentColor"/><path d="M4 8h6M7.5 5l3 3-3 3" stroke="#ddd0e2" stroke-width="2" fill="none"/></symbol>
  <symbol id="arrow-circle-light" viewBox="0 0 16 16"><circle cx="8" cy="8" r="8" fill="#ffffff"/><path d="M4 8h6M7.5 5l3 3-3 3" stroke="#555555" stroke-width="2" fill="none"/></symbol>
  <symbol id="chevrons" viewBox="0 0 10 10"><path d="M1 1l3 4-3 4M5 1l3 4-3 4" stroke="currentColor" stroke-width="1.3" fill="none"/></symbol>
</svg>

<header class="abs site-header">
  <div class="abs brand-badge">KOLVAN</div>
  <nav class="abs main-nav">
    <a class="is-current" href="#">HOME</a>
    <a href="#">WHAT WE DO</a>
    <a href="#">WHO WE ARE</a>
    <a href="#">SUCCESS STORIES</a>
    <a href="#">WHAT YOU CAN DO</a>
    <a href="#">DONATE &amp; JOIN</a>
  </nav>
</header>

<section class="abs hero" role="img" aria-label="Painted mountain valley at sunset with a river and pale silhouettes of a bird, a person with open arms and a bear"></section>
<h1 class="abs hero-title">HELP RAISE WORLD VIBRATION</h1>
<p class="abs hero-sub">Lorem ipsum dolor sit amet, consectetur adipiscing elit, sed do eiusmod</p>
<a class="abs btn hero-btn" href="#">MAKE A DIFFERENCE <svg><use href="#arrow-circle"/></svg></a>

<a class="abs cat-card environment" href="#" role="img" aria-label="Seedling growing from moss held in hands">
  <span class="abs cat-label"><span class="name">ENVIRONMENT</span><span class="more">FIND OUT MORE <svg><use href="#arrow-circle-light"/></svg></span></span>
</a>
<a class="abs cat-card animal" href="#" role="img" aria-label="Grey bear on a pale background">
  <span class="abs cat-label"><span class="name">ANIMAL</span><span class="more">FIND OUT MORE <svg><use href="#arrow-circle-light"/></svg></span></span>
</a>
<a class="abs cat-card human" href="#" role="img" aria-label="Woman standing in a modern office">
  <span class="abs cat-label"><span class="name">HUMAN</span><span class="more">FIND OUT MORE <svg><use href="#arrow-circle-light"/></svg></span></span>
</a>

<div class="abs feature-img environment" role="img" aria-label="Hand holding a glowing glass sphere with a plant, surrounded by eco icons"></div>
<h2 class="abs feature-title" style="left:643px;top:1108px">ENVIRONMENT</h2>
<p class="abs feature-text" style="left:645px;top:1161px">Lorem ipsum dolor sit amet, consectetur adipiscing elit, sed do eiusmod tempor incididunt ut labore et dolore magna aliqua. Ut enim ad minim veniam, quis nostrud exercitation ullamco laboris nisi ut aliquip ex ea commodo consequat. Duis aute irure dolor in reprehenderit in voluptate velit esse cillum dolore eu fugiat nulla pariatur. Excepteur sint occaecat cupidatat</p>
<a class="abs btn feature-btn" style="left:646px;top:1357px" href="#">LEARN MORE <svg><use href="#arrow-circle"/></svg></a>

<h2 class="abs feature-title" style="left:109px;top:1545px">ANIMAL</h2>
<p class="abs feature-text" style="left:111px;top:1598px">Lorem ipsum dolor sit amet, consectetur adipiscing elit, sed do eiusmod tempor incididunt ut labore et dolore magna aliqua. Ut enim ad minim veniam, quis nostrud exercitation ullamco laboris nisi ut aliquip ex ea commodo consequat. Duis aute irure dolor in reprehenderit in voluptate velit esse cillum dolore eu fugiat nulla pariatur. Excepteur sint occaecat cupidatat</p>
<a class="abs btn feature-btn" style="left:112px;top:1795px" href="#">LEARN MORE <svg><use href="#arrow-circle"/></svg></a>
<div class="abs feature-img animal" role="img" aria-label="Panda resting on a tree branch in a forest"></div>

<div class="abs feature-img human" role="img" aria-label="Smiling woman with a headscarf outdoors in warm sunlight"></div>
<h2 class="abs feature-title" style="left:643px;top:1982px">HUMAN</h2>
<p class="abs feature-text" style="left:645px;top:2035px">Lorem ipsum dolor sit amet, consectetur adipiscing elit, sed do eiusmod tempor incididunt ut labore et dolore magna aliqua. Ut enim ad minim veniam, quis nostrud exercitation ullamco laboris nisi ut aliquip ex ea commodo consequat. Duis aute irure dolor in reprehenderit in voluptate velit esse cillum dolore eu fugiat nulla pariatur. Excepteur sint occaecat cupidatat</p>
<a class="abs btn feature-btn" style="left:646px;top:2231px" href="#">LEARN MORE <svg><use href="#arrow-circle"/></svg></a>

<footer class="abs site-footer">
  <div class="abs footer-col" style="left:120px">
    <h3>GET INVOLVED</h3><div class="rule"></div>
    <ul>
      <li><svg><use href="#chevrons"/></svg>Join Us</li>
      <li><svg><use href="#chevrons"/></svg>Fundraise</li>
      <li><svg><use href="#chevrons"/></svg>Donate</li>
      <li><svg><use href="#chevrons"/></svg>Shop</li>
    </ul>
  </div>
  <div class="abs footer-col" style="left:359px">
    <h3>GET HELP</h3><div class="rule"></div>
    <ul>
      <li><svg><use href="#chevrons"/></svg>Contact Us</li>
      <li><svg><use href="#chevrons"/></svg>Media</li>
    </ul>
  </div>
  <div class="abs footer-col" style="left:597px">
    <h3>LEGAL</h3><div class="rule"></div>
    <ul>
      <li><svg><use href="#chevrons"/></svg>Terms and Conditions</li>
      <li><svg><use href="#chevrons"/></svg>Cookies</li>
      <li><svg><use href="#chevrons"/></svg>Privacy Policy</li>
    </ul>
  </div>
  <div class="abs footer-badge">KOLVAN</div>
  <div class="abs footer-divider"></div>
  <p class="abs copyright">© 2021 Kolvan. All Rights Reserved</p>
</footer>
</body>
</html>
```